Building company buisness cards

We are looking for a sharp modern new look for our business cards.
We are a New Zealand based company that specialises in house and land packages.
We have attached a photo of the current logo and would like to see if it can be improved somehow if needed.
We are open to any colours but we have chosen green at this stage.
Feel free to change the font and make the logo smarter looking.
Play with the colours and see what looks best.

We want a card that looks so good know one will want to throw it away!

Target Market(s)

Home buyers

Industry/Entity Type

Building

Contact Information for Business Card

Derek Tolvane
0217394062
dtolvane@quillmarkhomesteads.co.nz
quillmarkhomesteads.co.nz

Font styles to use
Serif
Sans Serif

Colors

Designer to choose colors to be used in the design.

Requirements
Must have
• Logo and company name on one side, details on the other side
Nice to have
• Color codes for the original green are HEX #4a8028, RGB(74,128,40), CMYK(42,0,69,50)
• Round corners, Raised and/or spot UV

```html
<!DOCTYPE html>
<html lang="en">
<head>
<meta charset="utf-8">
<title>Quillmark Homesteads – Business Cards</title>
<link href="https://fonts.googleapis.com/css2?family=Open+Sans:wght@400;600&display=swap" rel="stylesheet">
<style>
  :root {
    --backdrop: #e6e4e1;
    --card-white: #ffffff;
    --charcoal: #474747;
    --brand-green: #4a8028;
    --text-light: #f2f2f2;
  }
  * { margin: 0; padding: 0; box-sizing: border-box; }
  html, body {
    width: 1200px; height: 997px; overflow: hidden;
    background: var(--backdrop);
    font-family: "Open Sans", Arial, sans-serif;
  }
  .sheet {
    position: relative; width: 1200px; height: 997px;
    display: flex; flex-direction: column; align-items: center; justify-content: center; gap: 60px;
  }
  .card {
    position: relative; width: 720px; height: 400px; overflow: hidden;
    border-radius: 6px;
    box-shadow: 0 6px 18px rgba(0,0,0,0.12);
  }
  .card-front { background: var(--card-white); }
  .card-back { background: var(--charcoal); display: flex; align-items: center; justify-content: center; }

  .front-shapes { position: absolute; inset: 0; }

  .company-name { font-weight: 600; white-space: nowrap; }
  .front-company {
    position: absolute; left: 60px; top: 96px;
    color: var(--brand-green); font-size: 32px;
  }
  .back-company { color: var(--card-white); font-size: 42px; }

  .name-bar-label {
    position: absolute; left: 78px; top: 252px; height: 46px;
    display: flex; align-items: center;
    color: var(--card-white); font-weight: 600; font-size: 24px;
  }

  .contact-list {
    position: absolute; left: 432px; top: 174px;
    list-style: none; color: var(--text-light); font-size: 13px;
  }
  .contact-list li { display: flex; align-items: center; gap: 8px; height: 23px; white-space: nowrap; }
  .contact-list svg { width: 12px; height: 12px; flex: none; }
</style>
</head>
<body>
<main class="sheet">

  <section class="card card-front" aria-label="Card front with contact details">
    <svg class="front-shapes" viewBox="0 0 720 400" aria-hidden="true">
      <polygon points="420,148 720,148 720,400 300,400" fill="var(--charcoal)"/>
      <polygon points="48,252 412,252 388,298 48,298" fill="var(--brand-green)"/>
      <polygon points="388,298 412,252 420,252 400,298" fill="var(--card-white)"/>
    </svg>

    <div class="company-name front-company">Quillmark Homesteads</div>

    <div class="name-bar-label">Derek Tolvane</div>

    <ul class="contact-list">
      <li>
        <svg viewBox="0 0 16 16"><path d="M3 1l3 3-2 2c1 2 4 5 6 6l2-2 3 3-2 2C7 15 1 9 1 3z" fill="currentColor"/></svg>
        0217394062
      </li>
      <li>
        <svg viewBox="0 0 16 16"><rect x="1" y="3" width="14" height="10" fill="currentColor"/><path d="M1 3l7 6 7-6" fill="none" stroke="var(--charcoal)" stroke-width="1.5"/></svg>
        dtolvane@quillmarkhomesteads.co.nz
      </li>
      <li>
        <svg viewBox="0 0 16 16"><circle cx="8" cy="8" r="6.5" fill="none" stroke="currentColor" stroke-width="1.5"/><ellipse cx="8" cy="8" rx="2.8" ry="6.5" fill="none" stroke="currentColor" stroke-width="1.2"/><path d="M1.5 8h13" stroke="currentColor" stroke-width="1.2"/></svg>
        www.quillmarkhomesteads.co.nz
      </li>
    </ul>
  </section>

  <section class="card card-back" aria-label="Card back with company name">
    <div class="company-name back-company">Quillmark Homesteads</div>
  </section>

</main>
</body>
</html>
```